wealth management firm, professional group, new model

we have a logo that works but we need a card, white background using our colors...clean look

our tag line if can be used in

Steady Guidance for Lasting Wealth

```html
<!DOCTYPE html>
<html lang="en">
<head>
<meta charset="utf-8">
<title>Arcova Wealth Partners – Business Card</title>
<link href="https://fonts.googleapis.com/css2?family=Montserrat:wght@400;500;700&display=swap" rel="stylesheet">
<style>
  :root {
    --navy: #1b2a5c;
    --navy-deep: #111c40;
    --navy-light: #2b3f80;
    --white: #ffffff;
    --ink: #1b2a5c;
    --ink-soft: #3a4468;
    --backdrop: #e6e7ea;
  }
  * { box-sizing: border-box; margin: 0; padding: 0; }
  html, body { width: 1200px; height: 995px; overflow: hidden; }
  body {
    background: var(--backdrop);
    font-family: "Montserrat", Arial, sans-serif;
    position: relative;
  }
  .card {
    position: absolute;
    width: 560px;
    height: 320px;
    box-shadow: 0 14px 40px rgba(0,0,0,.18);
    overflow: hidden;
  }
  /* Front */
  .card-front { left: 320px; top: 110px; color: var(--white); }
  .card-front .texture {
    position: absolute; inset: 0;
    background: linear-gradient(135deg, var(--navy-light) 0%, var(--navy) 45%, var(--navy-deep) 100%);
  }
  .card-front .brand {
    position: absolute; inset: 0;
    display: flex; flex-direction: column; align-items: center; justify-content: center;
    text-align: center;
  }
  .brand-name {
    font-weight: 500; font-size: 46px; letter-spacing: 0.42em; margin-right: -0.42em;
  }
  .brand-sub {
    font-weight: 500; font-size: 15px; letter-spacing: 0.3em; margin-top: 14px; margin-right: -0.3em;
  }
  .tagline {
    font-weight: 500; font-size: 10.5px; letter-spacing: 0.24em; margin-top: 12px; margin-right: -0.24em;
  }
  /* Back */
  .card-back { left: 320px; top: 520px; background: var(--white); color: var(--ink); }
  .contact {
    position: absolute; left: 40px; top: 92px;
  }
  .person-name { font-weight: 700; font-size: 17px; letter-spacing: 0.01em; }
  .person-role { font-size: 13px; color: var(--ink-soft); margin-bottom: 16px; }
  .detail {
    display: flex; align-items: flex-start; gap: 8px;
    font-size: 12.5px; line-height: 1.35; color: var(--ink-soft); margin-bottom: 4px;
  }
  .detail svg { width: 12px; height: 12px; flex: none; margin-top: 2px; }
  .detail.address { margin-bottom: 12px; }
  .back-brand {
    position: absolute; right: 36px; top: 96px; text-align: center; color: var(--ink);
  }
  .back-brand .brand-name { font-size: 38px; }
  .back-brand .brand-sub { font-size: 12.5px; margin-top: 10px; }
  .band {
    position: absolute; left: 0; right: 0; bottom: 0; height: 30px;
    background: var(--navy);
  }
</style>
</head>
<body>
  <section class="card card-front">
    <div class="texture" role="img" aria-label="Faceted low-poly navy background texture"></div>
    <div class="brand">
      <div class="brand-name">ARCOVA</div>
      <div class="brand-sub">WEALTH PARTNERS</div>
      <div class="tagline">STEADY GUIDANCE FOR LASTING WEALTH</div>
    </div>
  </section>

  <section class="card card-back">
    <div class="contact">
      <div class="person-name">MARCO VELLANI</div>
      <div class="person-role">Brand Manager</div>
      <div class="detail address">
        <svg viewBox="0 0 12 12"><path fill="#1b2a5c" d="M6 0a4 4 0 0 0-4 4c0 3 4 8 4 8s4-5 4-8a4 4 0 0 0-4-4zm0 5.6a1.6 1.6 0 1 1 0-3.2 1.6 1.6 0 0 1 0 3.2z"/></svg>
        <span>Piazza Lumena 7<br>20135 Milano, Italy</span>
      </div>
      <div class="detail">
        <svg viewBox="0 0 12 12"><path fill="#1b2a5c" d="M2.4 0.6l2 2-1 1.4a7 7 0 0 0 4.6 4.6l1.4-1 2 2-1.4 1.8C5 11 1 7 .6 2z"/></svg>
        <span>+39.300.555.0142</span>
      </div>
      <div class="detail">
        <svg viewBox="0 0 12 12"><rect x="0.6" y="2" width="10.8" height="8" fill="none" stroke="#1b2a5c" stroke-width="1.2"/><path d="M0.6 2l5.4 4.4L11.4 2" fill="none" stroke="#1b2a5c" stroke-width="1.2"/></svg>
        <span>info@arcovamail.com</span>
      </div>
      <div class="detail">
        <svg viewBox="0 0 12 12"><circle cx="6" cy="6" r="5.3" fill="none" stroke="#1b2a5c" stroke-width="1"/><ellipse cx="6" cy="6" rx="2.3" ry="5.3" fill="none" stroke="#1b2a5c" stroke-width="1"/><path d="M0.7 6h10.6" stroke="#1b2a5c" stroke-width="1"/></svg>
        <span>www.arcovaweb.com</span>
      </div>
    </div>
    <div class="back-brand">
      <div class="brand-name">ARCOVA</div>
      <div class="brand-sub">WEALTH PARTNERS</div>
    </div>
    <div class="band"></div>
  </section>
</body>
</html>
```